Business Card for Industrial Distributor

We need a business card design for an industrial distributor. We sell machine parts for the manufacturing and oil industry. We would like the cards to look clean and modern but with a touch of industry.

Our colors are blue/white.

Please feel free to visit our website www.korvelpartsco.com

Target Market(s)

mexican manufacturers in the automobile/aerospace industry

Industry/Entity Type

Industrial

Colors
ffffff
0555a3

```html
<!DOCTYPE html>
<html lang="en">
<head>
<meta charset="utf-8">
<title>Korvel Business Card</title>
<link href="https://fonts.googleapis.com/css2?family=Open+Sans:wght@400;600;700;800&display=swap" rel="stylesheet">
<style>
  :root {
    --brand-blue: #2e3a92;
    --ink-grey: #4a4a4a;
    --card-white: #ffffff;
    --backdrop: #e6e6e6;
  }
  * { box-sizing: border-box; margin: 0; padding: 0; }
  html, body { width: 1200px; height: 900px; overflow: hidden; }
  body {
    background: var(--backdrop);
    font-family: "Open Sans", Arial, sans-serif;
    position: relative;
  }
  .card {
    position: absolute;
    top: 307px;
    width: 500px;
    height: 286px;
    border-radius: 3px;
    box-shadow: 0 2px 10px rgba(0,0,0,0.12);
  }
  .card--front { left: 70px; background: var(--card-white); }
  .card--back { left: 630px; background: var(--brand-blue); }

  .brand {
    position: absolute;
    display: flex;
    align-items: center;
    gap: 14px;
  }
  .brand__dot { border-radius: 50%; flex: none; }
  .brand__name { font-weight: 800; line-height: 1; letter-spacing: 0.5px; }

  .card--front .brand { left: 150px; top: 52px; }
  .card--front .brand__dot { width: 50px; height: 50px; background: var(--brand-blue); }
  .card--front .brand__name { font-size: 62px; color: var(--brand-blue); }

  .holder { position: absolute; left: 34px; top: 122px; color: var(--ink-grey); font-size: 12.5px; line-height: 1.35; }
  .holder__name { color: var(--brand-blue); font-weight: 600; font-size: 14px; letter-spacing: 0.5px; text-transform: uppercase; }

  .contacts { position: absolute; right: 32px; bottom: 34px; list-style: none; color: var(--ink-grey); font-size: 12.5px; line-height: 1.45; text-align: right; }
  .contacts li { display: flex; align-items: center; justify-content: flex-end; gap: 7px; }
  .contacts svg { width: 10px; height: 10px; fill: var(--brand-blue); }

  .card--back .brand { left: 50%; top: 96px; transform: translateX(-50%); }
  .card--back .brand__dot { width: 54px; height: 54px; background: var(--card-white); }
  .card--back .brand__name { font-size: 66px; color: var(--card-white); }
  .back-web { position: absolute; left: 0; right: 0; top: 196px; text-align: center; color: var(--card-white); font-size: 12px; letter-spacing: 0.3px; }
</style>
</head>
<body>
  <section class="card card--front" aria-label="Business card front">
    <div class="brand">
      <span class="brand__dot"></span>
      <span class="brand__name">Korvel</span>
    </div>
    <div class="holder">
      <p class="holder__name">Daniel Reyes</p>
      <p>Managing Director</p>
      <p>12345,your address goes here,</p>
      <p>country name 12345</p>
    </div>
    <ul class="contacts">
      <li>(044) 123 456 789 <svg viewBox="0 0 10 10"><path d="M2 1h2l1 2-1 1a5 5 0 0 0 2 2l1-1 2 1v2c0 1-1 1-1 1A8 8 0 0 1 1 2c0-1 1-1 1-1z"/></svg></li>
      <li>(044)123456789 <svg viewBox="0 0 10 10"><rect x="1.5" y="1" width="7" height="8" rx="1" fill="none" stroke="currentColor" stroke-width="1.4" style="stroke:var(--brand-blue)"/></svg></li>
      <li>info@youremail.com <svg viewBox="0 0 10 10"><path d="M1 2h8v6H1z"/><path d="M1 2l4 3 4-3" fill="none" stroke="#fff" stroke-width="0.9"/></svg></li>
      <li>www.webname.com <svg viewBox="0 0 10 10"><circle cx="5" cy="5" r="4"/></svg></li>
    </ul>
  </section>

  <section class="card card--back" aria-label="Business card back">
    <div class="brand">
      <span class="brand__dot"></span>
      <span class="brand__name">Korvel</span>
    </div>
    <p class="back-web">www.korvelpartsco.com</p>
  </section>
</body>
</html>
```